Business Card Update, need to bring life to the card, two sided color

We need a new business card design, are moving and changing addresses and need a new look, we have the logos already attached but need a new style moving forward. Can incorporate the color of the logo (The Green) as well, maybe a solid back? We deal with safety products revolving around static electricity and safety lighting. Would like to keep same font in second logo as well.

Target Market(s)

Electrical Safety, Lighting

Contact Information for Business Card

Dale Fenwick
Vice President
Office: 770-555-4821
Cell: 770-555-3067
dale@tkfenwick.example
www.tkfenwick.example
4700 West Harbor Boulevard
Suite #150
Roswell, GA 30076

Font styles to use
Serif
Sans Serif

Requirements
Must have
• Since 1918
Nice to have
• Could use the 100 Year Logo for back of card, would like the back of card to be the same green as logo.
Should not have
• No black cards please.

```html
<!DOCTYPE html>
<html lang="en">
<head>
<meta charset="utf-8">
<title>T. K. Fenwick Business Cards</title>
<link rel="stylesheet" href="https://fonts.googleapis.com/css2?family=Open+Sans:wght@300;400;600;700&display=swap">
<style>
  :root {
    --backdrop: #1b1b1c;
    --card-front: #f7f7f5;
    --card-edge: #dcdcd8;
    --green: #1fa463;
    --green-deep: #178a52;
    --ink: #2a2a2c;
    --muted: #6f6f72;
    --seal: #ecece9;
    --seal-ink: #c9c9c5;
    --on-green: #ffffff;
    --on-green-soft: #d8f1e4;
  }
  * { box-sizing: border-box; margin: 0; padding: 0; }
  html, body { width: 1200px; height: 672px; overflow: hidden; }
  body {
    background: var(--backdrop);
    font-family: "Open Sans", Arial, sans-serif;
    display: flex;
    align-items: center;
    justify-content: center;
    gap: 48px;
  }
  .card {
    position: relative;
    width: 540px;
    height: 309px;
    box-shadow: 0 14px 30px rgba(0,0,0,.55);
  }

  /* Contact side */
  .contact-side {
    background: var(--card-front);
    border: 1px solid var(--card-edge);
  }
  .contact-side .identity { position: absolute; left: 44px; top: 40px; }
  .person-name {
    color: var(--ink);
    font-size: 25px;
    letter-spacing: .5px;
    line-height: 1;
  }
  .person-name .first { font-weight: 300; }
  .person-name .last { font-weight: 700; }
  .person-title {
    margin-top: 6px;
    color: var(--green-deep);
    font-size: 11px;
    font-weight: 600;
    letter-spacing: 1px;
  }
  .contact-list {
    position: absolute;
    left: 44px;
    top: 124px;
    list-style: none;
  }
  .contact-list li {
    display: flex;
    align-items: center;
    gap: 9px;
    color: var(--ink);
    font-size: 13px;
    line-height: 1;
    height: 19px;
  }
  .contact-list svg { width: 11px; height: 11px; flex: none; }
  .contact-address {
    position: absolute;
    left: 44px;
    top: 216px;
    color: var(--ink);
    font-size: 13px;
    line-height: 19px;
  }
  .blind-seal {
    position: absolute;
    right: 40px;
    bottom: 34px;
    width: 124px;
    height: 124px;
    border-radius: 50%;
    background: var(--seal);
    display: flex;
    align-items: center;
    justify-content: center;
    text-align: center;
    color: var(--seal-ink);
    font-size: 13px;
    font-weight: 600;
    line-height: 1.3;
  }

  /* Brand side */
  .brand-side { background: var(--green); }
  .brand-side .brand {
    position: absolute;
    left: 52px;
    top: 74px;
    display: flex;
    align-items: center;
    gap: 18px;
  }
  .brand-dot {
    width: 74px;
    height: 74px;
    border-radius: 50%;
    background: var(--on-green);
    flex: none;
  }
  .brand-name {
    color: var(--on-green);
    font-weight: 600;
    line-height: 1.15;
  }
  .brand-name .primary { display: block; font-size: 27px; }
  .brand-name .secondary { display: block; font-size: 13px; }
  .brand-since {
    position: absolute;
    left: 144px;
    top: 166px;
    color: var(--on-green-soft);
    font-size: 11px;
    font-weight: 600;
    letter-spacing: 2px;
  }
  .brand-web {
    position: absolute;
    left: 52px;
    bottom: 52px;
    color: var(--on-green);
    font-size: 12px;
    letter-spacing: 3px;
  }
</style>
</head>
<body>

  <article class="card contact-side">
    <header class="identity">
      <h1 class="person-name"><span class="first">DALE</span> <span class="last">FENWICK</span></h1>
      <p class="person-title">VICE PRESIDENT</p>
    </header>
    <ul class="contact-list">
      <li>
        <svg viewBox="0 0 12 12" aria-hidden="true"><rect width="12" height="12" rx="1.5" fill="#1fa463"/><path d="M3.4 2.6c.4-.3.8-.2 1 .2l.7 1.3c.2.3 0 .7-.2.9l-.4.3c.4.9 1 1.5 1.9 1.9l.3-.4c.2-.3.6-.4.9-.2l1.3.7c.4.2.5.6.2 1l-.5.6c-.4.4-1 .5-1.6.3C5 8.4 3.6 7 2.9 5.1c-.2-.6-.1-1.2.3-1.6z" fill="#f7f7f5"/></svg>
        770-555-4821
      </li>
      <li>
        <svg viewBox="0 0 12 12" aria-hidden="true"><rect x="3" y="1" width="6" height="10" rx="1" fill="none" stroke="#1fa463" stroke-width="1.4"/><rect x="5" y="8.6" width="2" height="1" fill="#1fa463"/></svg>
        770-555-3067
      </li>
      <li>
        <svg viewBox="0 0 12 12" aria-hidden="true"><rect width="12" height="12" rx="1.5" fill="#1fa463"/><path d="M2.5 4l3.5 2.6L9.5 4" fill="none" stroke="#f7f7f5" stroke-width="1.2"/></svg>
        dale@tkfenwick.example
      </li>
      <li>
        <svg viewBox="0 0 12 12" aria-hidden="true"><circle cx="6" cy="6" r="5.5" fill="#1fa463"/><path d="M.8 6h10.4M6 .6c-2.2 2.8-2.2 8 0 10.8M6 .6c2.2 2.8 2.2 8 0 10.8" fill="none" stroke="#f7f7f5" stroke-width=".8"/></svg>
        www.tkfenwick.example
      </li>
    </ul>
    <p class="contact-address">4700 West Harbor Boulevard, Suite #150<br>Roswell, GA 30076</p>
    <div class="blind-seal">T. K.<br>Fenwick</div>
  </article>

  <article class="card brand-side">
    <div class="brand">
      <span class="brand-dot"></span>
      <p class="brand-name">
        <span class="primary">T. K. Fenwick</span>
        <span class="secondary">Manufacturing Company, Inc.</span>
      </p>
    </div>
    <p class="brand-since">SINCE 1918</p>
    <p class="brand-web">www.tkfenwick.example</p>
  </article>

</body>
</html>
```